Lawn Sign Design – Brisqel

We need a clean, eye-catching 18" x 24" lawn sign for Brisqel that effectively communicates our core message while maintaining strong brand consistency.

Key Elements to Include:
Tagline (Main Focus): Upgrade Your Roof Without Replacing It
Website: www.trybrisqel.com
Phone Number: (888) BRISQEL-GO
TWQB License Number: 4480512
Brisqel Logo & Branding: Ensure the logo, corporate colors, and custom font are used consistently to align with our existing branding.

Design Guidelines:
Simple & High-Impact: The tagline should be the most prominent element on the sign, drawing immediate attention.
Easy Readability: Use a bold, clean design with high contrast for quick readability from a distance.
Balanced Layout: Place supporting details (website, phone number, and TWQB number) in a visually clear but secondary position to the tagline.
Professional & Modern: The sign should reflect credibility and innovation in the roofing industry.

Deliverables:
High-resolution print-ready files (CMYK)
A digital proof for review before finalizing
The final design should make a strong impression with minimal text, ensuring that anyone passing by can instantly grasp what we offer.

I am including our custom font. To get an hexagon in our name, simply type the $ after the 'O" Please use this font for anything you type.

```html
<!DOCTYPE html>
<html lang="en">
<head>
<meta charset="utf-8">
<title>Brisqel Lawn Sign</title>
<link rel="stylesheet" href="https://fonts.googleapis.com/css2?family=Poppins:wght@300;500;600;700;800&display=swap">
<style>
  :root {
    --page-bg: #9b9b9b;
    --sign-white: #ffffff;
    --brand-blue: #1a56a4;
    --brand-blue-deep: #0d2f66;
    --ink: #1b1b1b;
    --roof-ink: #040f1f;
    --black: #000000;
  }
  * { margin: 0; padding: 0; box-sizing: border-box; }
  html, body { width: 1200px; height: 1200px; overflow: hidden; }
  body {
    background: var(--page-bg);
    font-family: "Poppins", sans-serif;
    position: relative;
  }
  .lawn-sign {
    position: absolute;
    left: 160px;
    top: 49px;
    width: 880px;
    height: 1102px;
    background: var(--sign-white);
  }
  .sign-shapes {
    position: absolute;
    inset: 0;
    width: 880px;
    height: 1102px;
  }
  .sign-text {
    position: absolute;
    left: 0;
    width: 100%;
    text-align: center;
    line-height: 1;
    white-space: nowrap;
  }
  .brand-name {
    top: 92px;
    font-size: 74px;
    font-weight: 700;
    color: var(--sign-white);
    letter-spacing: 3px;
  }
  .tagline-upgrade {
    top: 226px;
    font-size: 68px;
    font-weight: 800;
    color: var(--sign-white);
  }
  .tagline-roof {
    top: 280px;
    font-size: 152px;
    font-weight: 800;
    color: var(--roof-ink);
    letter-spacing: -2px;
  }
  .tagline-without {
    top: 428px;
    font-size: 52px;
    font-weight: 300;
    color: var(--sign-white);
    letter-spacing: 6px;
  }
  .tagline-replacing {
    top: 480px;
    font-size: 71px;
    font-weight: 800;
    color: var(--sign-white);
  }
  .phone-number {
    top: 896px;
    font-size: 70px;
    font-weight: 700;
    color: var(--ink);
  }
  .website {
    top: 972px;
    font-size: 60px;
    font-weight: 500;
    color: var(--ink);
    letter-spacing: 4px;
  }
  .website-name {
    font-weight: 700;
    color: var(--brand-blue);
  }
  .license-pill {
    position: absolute;
    left: 215px;
    top: 1057px;
    width: 450px;
    height: 42px;
    border-radius: 6px;
    background: var(--brand-blue);
    color: var(--sign-white);
    font-size: 24px;
    font-weight: 500;
    display: flex;
    align-items: center;
    justify-content: center;
  }
</style>
</head>
<body>
  <main class="lawn-sign">
    <svg class="sign-shapes" viewBox="0 0 1270 1590" xmlns="http://www.w3.org/2000/svg">
      <defs>
        <linearGradient id="panelGradient" x1="0" y1="0" x2="0" y2="1">
          <stop offset="0" stop-color="#1a56a4"/>
          <stop offset="1" stop-color="#0d2f66"/>
        </linearGradient>
        <linearGradient id="roofGradient" x1="0" y1="0" x2="0" y2="1">
          <stop offset="0" stop-color="#5d6b82"/>
          <stop offset="0.7" stop-color="#7c8696"/>
          <stop offset="1" stop-color="#b7b6b2"/>
        </linearGradient>
      </defs>
      <rect class="brand-panel" x="155" y="0" width="960" height="1224" fill="url(#panelGradient)"/>
      <polygon class="roof-photo" role="img" aria-label="Photo of a grey tiled hip roof on a house"
        points="155,895 325,846 470,895 640,935 800,935 1040,1060 1050,1110 1000,1224 155,1224"
        fill="url(#roofGradient)"/>
      <polygon class="white-chevron" points="155,1043 635,1255 1115,1037 1115,1590 155,1590" fill="#ffffff"/>
      <polygon class="corner-wedge-left" points="155,1046 400,1151 155,1224" fill="#000000"/>
      <polygon class="corner-wedge-right" points="1115,1040 870,1151 1115,1224" fill="#000000"/>
      <g class="phone-badge" transform="translate(635 1201)">
        <polygon points="0,-84 73,-42 73,42 0,84 -73,42 -73,-42" fill="#ffffff" stroke="#1a56a4" stroke-width="12" stroke-linejoin="round"/>
        <path d="M-28,-26 l12,-6 l10,20 l-8,7 q6,14 20,22 l7,-8 l20,10 l-5,13 q-6,6 -16,4 q-34,-10 -46,-44 q-2,-12 6,-18 z" fill="#111111"/>
        <path d="M6,-24 a20 20 0 0 1 18,18 M6,-34 a30 30 0 0 1 28,28" fill="none" stroke="#111111" stroke-width="3" stroke-linecap="round"/>
      </g>
    </svg>

    <div class="sign-text brand-name">BRISQEL</div>
    <h1 class="sign-text tagline-upgrade">UPGRADE YOUR</h1>
    <div class="sign-text tagline-roof">ROOF</div>
    <div class="sign-text tagline-without">WITHOUT</div>
    <div class="sign-text tagline-replacing">REPLACING IT</div>

    <div class="sign-text phone-number">(888) BRISQEL-GO</div>
    <div class="sign-text website">www.<span class="website-name">trybrisqel</span>.com</div>
    <div class="license-pill">TWQB License Number: 4480512</div>
  </main>
</body>
</html>
```